Business card update

Opening a subsidiary of my company in the USA and need to update my logo.
Updates

Reason: Give more time to a good design.

I made a mistake on my briefing. It's only the business card. Thanks for alerting me on the mistake.

All the best

Teodoro

Target Market(s)

We are an Executive Search company and our target audience are executives in large corporations.

Industry/Entity Type

Business

Requirements
Must have
• Keep the logo. In the US the company is called Delia Brunet Executive Search.

```html
<!DOCTYPE html>
<html lang="en">
<head>
<meta charset="UTF-8">
<title>Delia Brunet Executive Search – Business Card</title>
<link rel="stylesheet" href="https://fonts.googleapis.com/css2?family=Quicksand:wght@400;500;600&display=swap">
<style>
  :root {
    --bg: #e9ecec;
    --card-white: #ffffff;
    --teal: #45d6b4;
    --teal-deep: #2a9d85;
    --ink: #333333;
    --ink-soft: #2d5a50;
    --phone-red: #d8262a;
  }
  * { margin: 0; padding: 0; box-sizing: border-box; }
  html, body {
    width: 1200px; height: 741px; overflow: hidden;
    background: var(--bg);
    font-family: "Quicksand", sans-serif;
  }
  .stage {
    width: 1200px; height: 741px;
    display: flex; align-items: center; justify-content: center;
  }
  .card {
    position: relative;
    width: 400px; height: 700px;
    background: var(--card-white);
    overflow: hidden;
  }
  .card-wave { position: absolute; inset: 0; width: 400px; height: 700px; }
  .brand {
    position: absolute; top: 60px; left: 0; width: 100%;
    text-align: center;
    font-size: 30px; font-weight: 500;
    color: var(--ink);
  }
  .holder-name {
    position: absolute; top: 184px; left: 18px;
    font-size: 28px; font-weight: 500; color: var(--ink);
  }
  .contact-row {
    position: absolute; left: 18px;
    display: flex; align-items: center; gap: 8px;
  }
  .contact-row svg { flex: none; }
  .phone { top: 235px; font-size: 21px; font-weight: 500; color: var(--ink); }
  .web { top: 370px; font-size: 17px; color: var(--card-white); }
  .email { top: 399px; font-size: 17px; color: var(--card-white); }
  .company {
    position: absolute; top: 592px; left: 0; width: 100%;
    text-align: center;
    font-size: 25px; font-weight: 400; color: var(--teal-deep);
  }
  .address {
    position: absolute; top: 636px; left: 0; width: 100%;
    text-align: center; font-style: normal;
    font-size: 16px; line-height: 26px; font-weight: 500; color: var(--ink-soft);
  }
  .address-line { display: flex; align-items: center; gap: 12px; justify-content: center; }
  .address-line::before, .address-line::after {
    content: ""; flex: 1; height: 1px; background: var(--teal-deep); opacity: .6;
  }
  .address-line.plain::before, .address-line.plain::after { visibility: hidden; }
</style>
</head>
<body>
<main class="stage">
  <article class="card">
    <svg class="card-wave" viewBox="0 0 400 700" aria-hidden="true">
      <defs>
        <linearGradient id="waveShade" x1="0" y1="0" x2="1" y2="0">
          <stop offset="0" stop-color="#6e6e6e" stop-opacity=".85"/>
          <stop offset=".6" stop-color="#9a9a9a" stop-opacity=".35"/>
          <stop offset="1" stop-color="#ffffff" stop-opacity="0"/>
        </linearGradient>
        <filter id="soften" x="-10%" y="-10%" width="120%" height="120%">
          <feGaussianBlur stdDeviation="8"/>
        </filter>
      </defs>
      <path d="M0,330 C110,298 200,212 330,200 L400,198 L400,260 L0,360 Z" fill="url(#waveShade)" filter="url(#soften)"/>
      <path d="M0,345 C120,305 210,212 330,202 C360,199 385,198 400,198 L400,700 L0,700 Z" fill="var(--teal)"/>
    </svg>

    <div class="brand">Delia Brunet</div>

    <h1 class="holder-name">Teodoro S. Brunet</h1>

    <div class="contact-row phone">
      <svg width="16" height="20" viewBox="0 0 16 20" aria-hidden="true">
        <path d="M3,1 L6,1 L7,6 L5,7.5 C6,10.5 7.5,12.5 10,14 L11.5,12 L15,13.5 L14.5,17 C13,19 9,18.5 6,15 C2,11 0.5,6 3,1 Z" fill="var(--phone-red)"/>
      </svg>
      <span>305 555-0147</span>
    </div>

    <div class="contact-row web">
      <svg width="20" height="20" viewBox="0 0 20 20" aria-hidden="true">
        <circle cx="10" cy="10" r="8.5" fill="none" stroke="#ffffff" stroke-width="1.6"/>
        <ellipse cx="10" cy="10" rx="3.6" ry="8.5" fill="none" stroke="#ffffff" stroke-width="1.4"/>
        <path d="M1.5,10 H18.5 M3,5.5 H17 M3,14.5 H17" fill="none" stroke="#ffffff" stroke-width="1.2"/>
      </svg>
      <span>www.dbexecutivesearch.com</span>
    </div>

    <div class="contact-row email">
      <svg width="20" height="14" viewBox="0 0 20 14" aria-hidden="true">
        <rect x="0.5" y="0.5" width="19" height="13" fill="#ffffff"/>
        <path d="M1,1 L10,8 L19,1" fill="none" stroke="var(--teal)" stroke-width="1.5"/>
      </svg>
      <span>tbrunet@dbexecutivesearch.com</span>
    </div>

    <div class="company">Delia Brunet Executive Search</div>

    <address class="address">
      <div class="address-line">4820 Harbor Point Blvd Suite 310</div>
      <div class="address-line plain">Coral Bay FL 33190</div>
    </address>
  </article>
</main>
</body>
</html>
```